Carwash Signage

We own and operate a 25m tunnel car wash in the uk. We are looking to upgrade our signage to include the following:-

Wash selection Board Size-1300x1300mm
Conditions 1300x1300mm
Instructions 1300x1300mm
Banner 2600x600mm
Stamp card flyer a5 double sided - 9 squares for stamping 3rd square needs to say free air freshener 9th square needs to say free vip car wash.

I have attached some notes for the details that are required to be included.

We are looking for a modern smart look more European car wash style than American car wash style. It should be bold and clear. with yellow/orange & blue/green,grey colours

The final design must be in a industry standard printable format.

UPDATED BRIEF AS DISCUSSED: We require design for 2 x window decals, flag design and 50% off voucher. Attached are rough layout drawings of what they should look like - we expect the designs to be in keeping with the previous designs colours, etc that have been carried out. We Look forward to hearing from you.

Target Market(s)

local car owners within a 15-20 mile radius

Colors
0054AA
0677BA
7BADD7
CADEEF
E8F1F8
0094D4
00A9DD
6FCCEA
C7EBF8
E9F6FB
00AB8E
00BBA5
67D7C9
C6EFE9
E9F9F6

Requirements
Must have
• must be sharp and modern European look

```html
<!DOCTYPE html>
<html lang="en">
<head>
<meta charset="utf-8">
<title>Seabreeze Car Wash – Signage Set</title>
<link href="https://fonts.googleapis.com/css2?family=Bebas+Neue&family=Outfit:wght@400;600;700&family=Russo+One&display=swap" rel="stylesheet">
<style>
  :root{
    --backdrop:#a6a6a6;
    --navy-top:#0b1659;
    --navy-mid:#042f6e;
    --navy-low:#035f86;
    --card-navy:#04336b;
    --teal:#00c4b4;
    --teal-soft:#6fe0d2;
    --yellow:#fff200;
    --white:#ffffff;
    --heart:#e8202a;
    --foam-light:#eaf4fb;
    --foam-blue:#9cc3df;
  }
  html,body{margin:0;padding:0;width:1200px;height:1200px;overflow:hidden;background:var(--backdrop);}
  .sheet{position:relative;width:1200px;height:1200px;}
  .piece{position:absolute;display:block;}
  .voucher-front{left:140px;top:125px;width:436px;height:283px;}
  .voucher-back{left:623px;top:125px;width:437px;height:283px;}
  .poster{left:140px;top:461px;width:306px;height:613px;}
  .banner-attended{left:504px;top:461px;width:556px;height:278px;}
  .banner-love{left:504px;top:797px;width:556px;height:277px;}
  .brand-name{font-family:"Outfit",sans-serif;font-weight:700;fill:var(--white);}
  .brand-tag{font-family:"Outfit",sans-serif;font-weight:700;fill:var(--white);letter-spacing:2px;}
  .display{font-family:"Bebas Neue",sans-serif;}
  .sharp{font-family:"Russo One",sans-serif;font-style:italic;}
  .field-label{font-family:"Outfit",sans-serif;font-weight:600;font-size:16px;fill:var(--card-navy);}
  .small-print{font-family:"Outfit",sans-serif;font-weight:400;font-size:13.5px;fill:var(--white);}
</style>
</head>
<body>
<div class="sheet">
  <svg width="0" height="0" style="position:absolute">
    <defs>
      <linearGradient id="navyFade" x1="0" y1="0" x2="0" y2="1">
        <stop offset="0" stop-color="var(--navy-top)"/>
        <stop offset="0.6" stop-color="var(--navy-mid)"/>
        <stop offset="1" stop-color="var(--navy-low)"/>
      </linearGradient>
      <linearGradient id="foamFade" x1="0" y1="0" x2="0" y2="1">
        <stop offset="0" stop-color="var(--foam-blue)" stop-opacity="0"/>
        <stop offset="0.35" stop-color="var(--foam-blue)" stop-opacity="0.8"/>
        <stop offset="1" stop-color="var(--foam-light)"/>
      </linearGradient>
      <linearGradient id="vipFill" x1="0" y1="0" x2="1" y2="0">
        <stop offset="0" stop-color="var(--teal)"/>
        <stop offset="1" stop-color="var(--teal-soft)"/>
      </linearGradient>
      <path id="chevron" d="M35 0H58L23 35L58 70H35L0 35Z"/>
      <path id="heart" d="M0 -18C-6 -32 -34 -30 -34 -6C-34 12 -10 30 0 44C10 30 34 12 34 -6C34 -30 6 -32 0 -18Z"/>
    </defs>
  </svg>

  <!-- Voucher front -->
  <svg class="piece voucher-front" viewBox="0 0 436 283">
    <clipPath id="frontClip"><rect width="436" height="283" rx="18"/></clipPath>
    <g clip-path="url(#frontClip)">
      <rect width="436" height="283" fill="url(#navyFade)"/>
      <rect y="175" width="436" height="108" fill="url(#foamFade)" role="img" aria-label="Soap foam and bubbles"/>
    </g>
    <text class="brand-tag" x="304" y="41" font-size="11" text-anchor="end">CAR WASH</text>
    <text class="brand-name" x="218" y="70" font-size="29" text-anchor="middle" textLength="206" lengthAdjust="spacingAndGlyphs">SEABREEZE</text>
    <path d="M79 209L346 209L336 218L73 218Z" fill="var(--navy-top)"/>
    <rect x="66" y="102" width="314" height="104" rx="12" fill="var(--teal)" transform="skewX(-5)"/>
    <text class="display" x="83" y="193" font-size="108" fill="var(--card-navy)" textLength="284" lengthAdjust="spacingAndGlyphs">50% OFF</text>
    <text class="sharp" x="65" y="254" font-size="30" fill="url(#vipFill)" stroke="var(--card-navy)" stroke-width="1.2" textLength="308" lengthAdjust="spacingAndGlyphs">VIP WASH</text>
  </svg>

  <!-- Voucher back -->
  <svg class="piece voucher-back" viewBox="0 0 437 283">
    <rect width="437" height="283" rx="18" fill="var(--card-navy)"/>
    <text class="brand-tag" x="315" y="36" font-size="11" text-anchor="end">CAR WASH</text>
    <text class="brand-name" x="230" y="65" font-size="29" text-anchor="middle" textLength="206" lengthAdjust="spacingAndGlyphs">SEABREEZE</text>
    <g class="form-row">
      <rect x="24" y="92" width="135" height="29" rx="4" fill="var(--teal)"/>
      <text class="field-label" x="32" y="112">Vehicle Reg</text>
      <text class="field-label" x="167" y="111" fill="var(--white)">:</text>
      <rect x="175" y="92" width="239" height="29" rx="4" fill="var(--white)"/>
    </g>
    <g class="form-row">
      <rect x="24" y="136" width="135" height="29" rx="4" fill="var(--teal)"/>
      <text class="field-label" x="32" y="156">Operator</text>
      <text class="field-label" x="167" y="155" fill="var(--white)">:</text>
      <rect x="175" y="136" width="239" height="29" rx="4" fill="var(--white)"/>
    </g>
    <g class="form-row">
      <rect x="24" y="179" width="135" height="29" rx="4" fill="var(--teal)"/>
      <text class="field-label" x="32" y="199">Date</text>
      <text class="field-label" x="167" y="198" fill="var(--white)">:</text>
      <rect x="175" y="179" width="239" height="29" rx="4" fill="var(--white)"/>
    </g>
    <text class="small-print" x="219" y="248" text-anchor="middle">VALID FOR 10 DAYS FROM ABOVE DATE</text>
  </svg>

  <!-- Vertical poster -->
  <svg class="piece poster" viewBox="0 0 306 613">
    <rect width="306" height="613" fill="url(#navyFade)"/>
    <text class="display" x="31" y="196" font-size="205" fill="var(--teal)" textLength="246" lengthAdjust="spacingAndGlyphs">WE</text>
    <text class="display" x="31" y="311" font-size="128" fill="var(--teal)" textLength="246" lengthAdjust="spacingAndGlyphs">L&#8202;&#8202;&#8202;&#8202;&#8202;&#8202;&#8202;&#8202;VE</text>
    <use href="#heart" transform="translate(110 260) scale(1.2)" fill="var(--heart)"/>
    <text class="sharp" x="31" y="394" font-size="62" fill="var(--white)" textLength="246" lengthAdjust="spacingAndGlyphs">DIRTY</text>
    <text class="sharp" x="31" y="480" font-size="76" fill="var(--white)" textLength="244" lengthAdjust="spacingAndGlyphs">CARS</text>
    <path d="M0 531H140C150 531 154 515 170 511H306V613H0Z" fill="var(--teal)"/>
    <text class="brand-tag" x="275" y="550" font-size="13" text-anchor="end">CAR WASH</text>
    <text class="brand-name" x="153" y="585" font-size="34" text-anchor="middle" textLength="256" lengthAdjust="spacingAndGlyphs">SEABREEZE</text>
  </svg>

  <!-- Attended banner -->
  <svg class="piece banner-attended" viewBox="0 0 556 278">
    <rect width="556" height="176" fill="url(#navyFade)"/>
    <rect y="175" width="556" height="103" fill="var(--teal)"/>
    <text class="sharp" x="32" y="71" font-size="28" fill="var(--teal)" textLength="234" lengthAdjust="spacingAndGlyphs">ATTENDED</text>
    <text class="brand-tag" x="515" y="36" font-size="11" text-anchor="end">CAR WASH</text>
    <text class="brand-name" x="420" y="65" font-size="28" text-anchor="middle" textLength="196" lengthAdjust="spacingAndGlyphs">SEABREEZE</text>
    <text class="sharp" x="32" y="150" font-size="74" fill="var(--white)" textLength="492" lengthAdjust="spacingAndGlyphs">CARWASH</text>
    <g class="chevrons" transform="translate(30 192)">
      <use href="#chevron" x="0" fill="var(--yellow)"/>
      <use href="#chevron" x="55" fill="var(--white)"/>
      <use href="#chevron" x="110" fill="var(--yellow)"/>
      <use href="#chevron" x="165" fill="var(--white)"/>
      <use href="#chevron" x="220" fill="var(--yellow)"/>
      <use href="#chevron" x="275" fill="var(--white)"/>
      <use href="#chevron" x="330" fill="var(--yellow)"/>
      <use href="#chevron" x="385" fill="var(--white)"/>
      <use href="#chevron" x="440" fill="var(--yellow)"/>
    </g>
  </svg>

  <!-- We love dirty cars banner -->
  <svg class="piece banner-love" viewBox="0 0 556 277">
    <rect width="556" height="175" fill="url(#navyFade)"/>
    <rect y="174" width="556" height="103" fill="var(--teal)"/>
    <text class="brand-tag" x="403" y="30" font-size="13" text-anchor="end">CAR WASH</text>
    <text class="brand-name" x="282" y="67" font-size="35" text-anchor="middle" textLength="262" lengthAdjust="spacingAndGlyphs">SEABREEZE</text>
    <text class="display" x="32" y="157" font-size="98" fill="var(--teal)" textLength="338" lengthAdjust="spacingAndGlyphs">WE L&#8202;&#8202;&#8202;&#8202;&#8202;&#8202;&#8202;&#8202;VE</text>
    <use href="#heart" transform="translate(235 118) scale(1.02)" fill="var(--heart)"/>
    <text class="sharp" x="382" y="120" font-size="40" fill="var(--white)" textLength="146" lengthAdjust="spacingAndGlyphs">DIRTY</text>
    <text class="sharp" x="390" y="157" font-size="42" fill="var(--white)" textLength="130" lengthAdjust="spacingAndGlyphs">CARS</text>
    <g class="chevrons" transform="translate(30 192)">
      <use href="#chevron" x="0" fill="var(--yellow)"/>
      <use href="#chevron" x="55" fill="var(--white)"/>
      <use href="#chevron" x="110" fill="var(--yellow)"/>
      <use href="#chevron" x="165" fill="var(--white)"/>
      <use href="#chevron" x="220" fill="var(--yellow)"/>
      <use href="#chevron" x="275" fill="var(--white)"/>
      <use href="#chevron" x="330" fill="var(--yellow)"/>
      <use href="#chevron" x="385" fill="var(--white)"/>
      <use href="#chevron" x="440" fill="var(--yellow)"/>
    </g>
  </svg>
</div>
</body>
</html>
```